Flyer-Design für Hundephysiopraxis
Zielgruppe
Ich bin selbstständige Hundephysiotherapeutin / Hundeosteopathin /Hundefitnesstrainerin. Meine Zielgruppe sind Hundehalter bzw. allgemein Tierhalter (biete noch weitere Dinge für Hunde/Tiere an) aber auch Tierärzte.
Aufgabenstellung
Es wäre schön, wenn Sie die Texte ähnlich wie auf meiner Homepage gestalten (z.B. Infos aus der Startseite oder Therapieformen).
Prinzipiell sollte es eher natürlich, freundlich und nett gestaltet sein. Schlichtere Farben passend zum Logo.
Homepage: www.pfotenruhe-mitte.de
Bei den Maßen bin ich offen, hatte aber eher an diesen 'typischen Flyer' gedacht (3 seitiger Flyer mit Vorder und Rückseite) bin aber prinzipiell offen :)
Einen Beispiel Flyer habe ich drangehängt sowie z.B. schon ein paar Fotos die man ggf nutzen kann. Weitere Behandlunsfotos kann ich gerne nachreichen.
Die Flyer sollen hauptsächlich bei z.B. Tierärzten / Tierklinik / Tiernahrungsmärkte wie Kornbeutel ausgelegt werden damit Menschen die mich noch nicht kennen auf meine Arbeit aufmerksam werden.

```html
<!DOCTYPE html>
<html lang="de">
<head>
<meta charset="utf-8">
<title>Pfotenruhe Mitte – Flyer</title>
<link href="https://fonts.googleapis.com/css2?family=Open+Sans:wght@400;500&family=Roboto+Condensed:wght@400&display=swap" rel="stylesheet">
<style>
:root{
  --bg:#f1f1f1;
  --paper:#ffffff;
  --ink:#1e1e1e;
  --teal-dark:#0e8a8c;
  --teal:#12a3b5;
  --teal-band:#05a5b2;
  --teal-deep:#17959f;
  --teal-soft:#a8dfe6;
  --blue:#1769a0;
  --blue-deep:#175d91;
  --purple:#7a3e99;
  --lilac:#8a5ba5;
  --orange:#e8671a;
}
*{margin:0;padding:0;box-sizing:border-box}
html,body{width:849px;height:1200px;overflow:hidden;background:var(--bg)}
body{position:relative;font-family:"Open Sans",sans-serif;color:var(--ink)}

.page{position:absolute;background:var(--paper);box-shadow:0 6px 18px rgba(80,60,50,.28)}
.page--inside{left:120px;top:70px;width:620px;height:440px}
.page--cover{left:210px;top:555px;width:440px;height:619px;overflow:hidden}

/* Inside page: therapy wheel */
.wheel-lines{position:absolute;left:0;top:0}
.therapy{position:absolute;width:153px}
.therapy__title{font-size:11px;line-height:12px;font-weight:400;white-space:nowrap;margin-bottom:3px}
.therapy__text{font-size:6.6px;line-height:8.6px;text-align:justify;hyphens:auto}
.therapy--teal-dark .therapy__title{color:var(--teal-dark)}
.therapy--teal .therapy__title{color:var(--teal)}
.therapy--blue .therapy__title{color:var(--blue)}
.therapy--blue-deep .therapy__title{color:var(--blue-deep)}
.therapy--purple .therapy__title{color:var(--purple)}
.therapy--lilac .therapy__title{color:var(--lilac)}

.therapy--featured{border:3px solid var(--teal-soft);padding:4px 6px 6px 5px;width:171px}
.therapy--featured .therapy__title{font-size:15px;line-height:17px;color:var(--teal);margin-bottom:3px}

/* Cover page */
.cover-photo{position:absolute;left:0;top:0}
.brand{position:absolute;left:0;top:280px;width:440px;text-align:center}
.brand__name{font-size:17px;color:var(--orange);font-weight:400;letter-spacing:.3px}
.brand__tagline{font-size:6.5px;letter-spacing:2.6px;color:var(--orange);margin-top:4px;line-height:9px}
.cover-band{position:absolute;left:0;top:335px;width:440px;height:29px;background:var(--teal-band);color:#fff;font-size:16.5px;line-height:29px;text-align:center}
.cover-footer{position:absolute;left:0;top:364px;width:440px;height:255px;background:var(--teal-deep)}
.contact{position:absolute;left:18px;top:14px;width:181px;height:224px;background:var(--paper);font-family:"Roboto Condensed",sans-serif;font-size:9px;line-height:11.3px;padding:5px 12px 0 6px}
.contact__title{font-size:13px;line-height:16px;margin-bottom:2px}
.contact__rule{height:1px;background:var(--teal);margin:4px 0 5px}
.contact__map{position:absolute;left:0;bottom:0;width:181px;height:82px}
.dog-photo{position:absolute;left:199px;top:14px;width:224px;height:224px}
</style>
</head>
<body>

<!-- Inside page -->
<section class="page page--inside">
  <svg class="wheel-lines" width="620" height="440" viewBox="0 0 620 440">
    <defs>
      <marker id="arrow" viewBox="0 0 10 10" refX="9" refY="5" markerWidth="6" markerHeight="6" orient="auto">
        <path d="M0 0 L10 5 L0 10 z" fill="context-stroke"/>
      </marker>
    </defs>
    <!-- wheel segments -->
    <g fill="none" stroke-width="24">
      <circle cx="310" cy="220" r="68" stroke="#1178b8" stroke-dasharray="28.5 399" transform="rotate(-87 310 220)"/>
      <circle cx="310" cy="220" r="68" stroke="#1766a3" stroke-dasharray="28.5 399" transform="rotate(-57 310 220)"/>
      <circle cx="310" cy="220" r="68" stroke="#175d91" stroke-dasharray="28.5 399" transform="rotate(-27 310 220)"/>
      <circle cx="310" cy="220" r="68" stroke="#15578a" stroke-dasharray="28.5 399" transform="rotate(3 310 220)"/>
      <circle cx="310" cy="220" r="68" stroke="#9c75b5" stroke-dasharray="28.5 399" transform="rotate(33 310 220)"/>
      <circle cx="310" cy="220" r="68" stroke="#8a5ba5" stroke-dasharray="28.5 399" transform="rotate(63 310 220)"/>
      <circle cx="310" cy="220" r="68" stroke="#6b3690" stroke-dasharray="28.5 399" transform="rotate(93 310 220)"/>
      <circle cx="310" cy="220" r="68" stroke="#16a6b6" stroke-dasharray="28.5 399" transform="rotate(123 310 220)"/>
      <circle cx="310" cy="220" r="68" stroke="#13a5b8" stroke-dasharray="28.5 399" transform="rotate(153 310 220)"/>
      <circle cx="310" cy="220" r="68" stroke="#11a0b2" stroke-dasharray="28.5 399" transform="rotate(183 310 220)"/>
      <circle cx="310" cy="220" r="68" stroke="#0f98a5" stroke-dasharray="28.5 399" transform="rotate(213 310 220)"/>
      <circle cx="310" cy="220" r="68" stroke="#0e8789" stroke-dasharray="28.5 399" transform="rotate(243 310 220)"/>
    </g>
    <circle cx="310" cy="220" r="46" fill="#d6eff2" role="img" aria-label="Illustration eines springenden Hundes in Türkis"/>

    <!-- connectors -->
    <g fill="none" stroke-width="0.9" marker-end="url(#arrow)">
      <polyline points="114,35 271,35 286,139" stroke="var(--teal-dark)"/>
      <polyline points="37,134 195,134 243,167" stroke="var(--teal)"/>
      <polyline points="56,204 208,204 226,217" stroke="var(--teal)"/>
      <polyline points="69,269 234,269 241,267" stroke="var(--teal)"/>
      <polyline points="109,347 264,347 281,300" stroke="var(--purple)"/>
      <polyline points="508,69 354,69 337,140" stroke="var(--blue)"/>
      <polyline points="569,156 412,156 381,171" stroke="var(--blue)"/>
      <polyline points="569,208 411,208 395,217" stroke="var(--blue-deep)"/>
      <polyline points="569,285 410,285 378,271" stroke="var(--lilac)"/>
      <polyline points="532,357 373,357 338,300" stroke="var(--lilac)"/>
    </g>
  </svg>

  <article class="therapy therapy--teal-dark" style="left:117px;top:21px">
    <h3 class="therapy__title">Breuß-Massage</h3>
    <p class="therapy__text">Bei der Breuß-Massage wird die Wirbelsäule durch eine wohltuende Massage am Kreuzbein entspannt und gestreckt. Durch gezielte Griffe und Dehnungen wird der Rücken gelockert und verschobene Wirbel schmerzfrei in die ursprüngliche Position gebracht.</p>
  </article>

  <article class="therapy therapy--featured" style="left:29px;top:111px">
    <h2 class="therapy__title">Hundephysiotherapie</h2>
    <p class="therapy__text">Aktivierung von Stoffwechsel und Durchblutung Schmerzlinderung keimabtötend Stimulierung der Angioneogenese (Neubildung von Zellen und Gewebe)</p>
  </article>

  <article class="therapy therapy--teal" style="left:56px;top:191px">
    <h3 class="therapy__title">Hundeosteopathie</h3>
    <p class="therapy__text">Aktuell befinde ich mich in der Ausbildung zur Hundeosteopathin. Natürlich werde ich schon jetzt einige gelernte Anwendungen in meiner Behandlung miteinfließen lassen. Prüfung voraussichtlich im Mai 2023</p>
  </article>

  <article class="therapy therapy--teal" style="left:69px;top:256px">
    <h3 class="therapy__title">Dorn Therapie</h3>
    <p class="therapy__text">Die Wirbelsäulentherapie nach Dorn, ist eine sanfte Methode, die zur Behandlung von Beschwerden des Bewegungsapparates zum Einsatz kommt. Der Therapeut bringt in der Therapiesitzung Wirbel und Gelenke mit sanften und einfühlsamen Bewegungen in ihre richtige Position zurück.</p>
  </article>

  <article class="therapy therapy--purple" style="left:109px;top:334px">
    <h3 class="therapy__title">Blutegeltherapie</h3>
    <p class="therapy__text">Das Speichel-Sekret des Blutegels, welches beim Beissen in die Wunde des Tieres gelangt, wirkt entzündungs- und gerinnungshemmend, schmerzlindernd und regt den Lymphfluss an.</p>
  </article>

  <article class="therapy therapy--blue" style="left:358px;top:56px">
    <h3 class="therapy__title">Hundefitnesstrainer</h3>
    <p class="therapy__text">Perfekte Ergänzung nach erfolgreicher Hundephysiotherapie, individuelle Trainingspläne Muskelaufbautraining, Beweglichkeitstraining, Abnehmtraining, Fitnesstraining, Gehirntraining, Schult den optimalen Bewegungsablauf, Tipps und Training für Sporthunde, z.B. mit Cavaletti oder Balancepads</p>
  </article>

  <article class="therapy therapy--blue" style="left:416px;top:143px">
    <h3 class="therapy__title">Mykotherapie</h3>
    <p class="therapy__text" style="text-align:left">Oder auch vereinfacht gesagt: Das Heilen mit Pilzen Informationen hierzu folgen.</p>
  </article>

  <article class="therapy therapy--blue-deep" style="left:415px;top:195px">
    <h3 class="therapy__title">Edelsteintherapie</h3>
    <p class="therapy__text">Unsere Tiere reagieren auf unser Umfeld sensibler, als wir Menschen. Bei der Edelsteintherapie wird davon ausgegangen, dass die Heilsteine die Fähigkeiten besitzen seelische und körperliche Beschwerden zu mindern.</p>
  </article>

  <article class="therapy therapy--lilac" style="left:417px;top:272px">
    <h3 class="therapy__title">Tierkommunikation</h3>
    <p class="therapy__text">Nicht nur wir Menschen kämpfen oft mit seelischen Belastungen, unseren Tieren geht es häufig genauso. Durch eine Tierkommunikation ist es möglich, mit den Tieren in Kontakt zu treten und solche Belastungen zu erkennen.</p>
  </article>

  <article class="therapy therapy--lilac" style="left:382px;top:344px">
    <h3 class="therapy__title">Bachblütenberatung</h3>
    <p class="therapy__text" style="margin-top:2px">Bachblüten sind Extrakte aus Blüten, die auf störende Emotionen und Gefühle wie z.B. (Trennungs-)Angst, Unsicherheit, Agression, Stress usw. positiv einwirken. Sie können bei Silvester, einer langen Autoreise, Umzug oder dem Tierarztbesuch unterstützen.</p>
  </article>
</section>

<!-- Cover page -->
<section class="page page--cover">
  <svg class="cover-photo" width="440" height="270" viewBox="0 0 440 270">
    <defs>
      <linearGradient id="garden" x1="0" y1="0" x2="0" y2="1">
        <stop offset="0" stop-color="#c9d7a8"/>
        <stop offset="0.45" stop-color="#6f9a52"/>
        <stop offset="1" stop-color="#4f7a3a"/>
      </linearGradient>
    </defs>
    <path d="M0 0 H440 V123 L52 244 Q42 247 38 236 L0 120 Z" fill="url(#garden)" role="img" aria-label="Foto: Therapeutin sitzt mit zwei Hunden im Gras eines eingezäunten Gartens"/>
    <path d="M0 120 L38 236 Q44 252 62 245 L440 128" fill="none" stroke="var(--teal)" stroke-width="5"/>
  </svg>

  <div class="brand">
    <div class="brand__name">Pfotenruhe Mitte</div>
    <div class="brand__tagline">Hundephysiotherapie<br>Mareike Holtmann</div>
  </div>

  <div class="cover-band">Hundephysiotherapie &amp; Hundeosteopathie</div>

  <div class="cover-footer">
    <div class="contact">
      <h2 class="contact__title">Kontakt</h2>
      <p>www.pfotenruhe-mitte.de<br>E-mail: info@pfotenruhe-mitte.de</p>
      <div class="contact__rule"></div>
      <p>Handy: 0176 48213907<br>gerne auch per<br>SMS oder Messenger</p>
      <div class="contact__rule"></div>
      <p>Anschrift:<br>Mareike Holtmann,<br>Birkenweg 7,<br>35390 Talheim</p>
      <svg class="contact__map" viewBox="0 0 181 82" role="img" aria-label="Kartenausschnitt mit Standort der Praxis">
        <rect width="181" height="82" fill="#eef0f2"/>
      </svg>
    </div>
    <svg class="dog-photo" viewBox="0 0 224 224" role="img" aria-label="Foto eines schwarz-weiß gesprenkelten Spaniels im Garten">
      <defs>
        <linearGradient id="lawn" x1="0" y1="0" x2="1" y2="1">
          <stop offset="0" stop-color="#5e6a4a"/>
          <stop offset="0.5" stop-color="#8fb04e"/>
          <stop offset="1" stop-color="#7ba43f"/>
        </linearGradient>
      </defs>
      <rect width="224" height="224" fill="url(#lawn)"/>
    </svg>
  </div>
</section>

</body>
</html>
```